Hula-Hoop dance entertainment sales and instruction by spin-wavelet needs a business card

I need a 2 sided business card that is square (although this is not an absolute )for my self employed business as an independent artist. my business name is "Spin-Wavelet" I teach how to hula-hoop classes, make and sell hula-hoops, provided entertainment at kids birthday parties, community events, corporate events and perform at artistic dance shows.
I would like to see spirals or curved lines in the card, and I would like the card to be seen as fun, spunky, flair and eye catching.

the card could double as a tag to go on the hoops i sell,

Target Market(s)

women age 20 - 50

Industry/Entity Type

Entertainment

Requirements
Must have
• Dorine Vantash
www.spinwavelet.example
555.014.7263
Nice to have
• I would like my image to be on one side of the card. so people can recognize me!

```html
<!DOCTYPE html>
<html lang="en">
<head>
<meta charset="utf-8">
<title>Spin-Wavelet – Dorine Vantash</title>
<link rel="stylesheet" href="https://fonts.googleapis.com/css2?family=Chewy&family=Open+Sans:wght@700&display=swap">
<style>
  :root {
    --canvas: #ffffff;
    --card-pink: #e39bb8;
    --frame-black: #0a0a0a;
    --ring-purple: #6a43a3;
    --ring-blue: #6b8fc6;
    --oval-cyan: rgba(128, 213, 225, 0.75);
    --oval-edge: #a3cf7a;
    --title-ink: #111111;
    --name-ink: #000000;
    --photo-warm: #d9b7a6;
    --photo-cool: #bfb9bb;
  }
  html, body {
    margin: 0;
    padding: 0;
    width: 1200px;
    height: 1165px;
    overflow: hidden;
    background: var(--canvas);
  }
  .card-canvas {
    width: 1200px;
    height: 1165px;
    display: block;
  }
  .card-square { fill: var(--card-pink); stroke: var(--frame-black); stroke-width: 9; }
  .spin-ring { fill: none; stroke: var(--ring-purple); stroke-width: 4.5; }
  .spin-ring--soft { stroke: var(--ring-blue); }
  .title-oval { fill: var(--oval-cyan); stroke: var(--oval-edge); stroke-width: 4; }
  .brand-title {
    font-family: "Chewy", "Comic Sans MS", cursive;
    font-size: 150px;
    fill: var(--title-ink);
    letter-spacing: 6px;
  }
  .artist-name {
    font-family: "Open Sans", Arial, sans-serif;
    font-weight: 700;
    font-size: 40px;
    fill: var(--name-ink);
  }
  .contact-line {
    font-family: "Open Sans", Arial, sans-serif;
    font-weight: 700;
    font-size: 24px;
    fill: var(--name-ink);
  }
</style>
</head>
<body>
<svg class="card-canvas" viewBox="0 0 1200 1165" xmlns="http://www.w3.org/2000/svg">
  <defs>
    <linearGradient id="portraitTone" x1="0" y1="0" x2="1" y2="1">
      <stop offset="0" stop-color="var(--photo-warm)"/>
      <stop offset="1" stop-color="var(--photo-cool)"/>
    </linearGradient>
  </defs>

  <rect class="card-square" x="122" y="142" width="922" height="920"/>

  <rect class="portrait" role="img" aria-label="Photo of Dorine Vantash holding a hula hoop over her shoulder"
        x="330" y="590" width="710" height="468" rx="24" fill="url(#portraitTone)" opacity="0.85"/>

  <g class="hoop-rings">
    <circle class="spin-ring" cx="660" cy="271" r="267"/>
    <circle class="spin-ring" cx="852" cy="345" r="345"/>
    <circle class="spin-ring spin-ring--soft" cx="474" cy="555" r="237"/>
    <circle class="spin-ring" cx="284" cy="778" r="172"/>
    <circle class="spin-ring" cx="530" cy="866" r="203"/>
    <circle class="spin-ring" cx="165" cy="998" r="162"/>
  </g>

  <ellipse class="title-oval" cx="599" cy="392" rx="602" ry="165" transform="rotate(-11 599 392)"/>

  <g class="brand-block">
    <text class="brand-title" x="170" y="450" transform="rotate(-10 170 450)">Spin-</text>
    <text class="brand-title" x="395" y="555" transform="rotate(-10 395 555)">Wavelet</text>
  </g>

  <g class="artist-block">
    <text class="artist-name" x="413" y="830">Dorine</text>
    <text class="artist-name" x="413" y="876">Vantash</text>
    <text class="contact-line" x="413" y="918">www.spinwavelet.example</text>
    <text class="contact-line" x="413" y="950">555.014.7263</text>
  </g>
</svg>
</body>
</html>
```